Onboarding Carousel UI/UX design

We need a great UI/UX design for our onboarding carousel as attached in the PDF document. The chosen designers will be given our brand book with colors and styles to be used. The images must be focused on the content of each slide and be professional unique style (Do not use the childish cartoons we have used for placeholders)

Industry/Entity Type

Mortgage Brokerage

Number of Pages Required

5+ page

Font styles to use
Other font styles liked:
• Roboto

Requirements
Must have
• Great UI / UX design
Very relevant content of the images to match the slide
Nice to have
• Brand book

https://pv.lumorak.com/view/ed991dda-3474-4c3e-9747-882e21ba3df5-b8ca/?fullscreen

Image styles we like. Would need to be customized and made unique for us.

https://pinvarlo.com/shots/6300615-Torvane-Quillet-Illustration-Collaboration
https://meltridgestudio.co.za/software-client-style-frames
Should not have
• Do not use the childish images we have used as placeholders

```html
<!DOCTYPE html>
<html lang="en">
<head>
<meta charset="utf-8">
<title>Onboarding Carousel — Meridale Brokers Apply Online</title>
<link rel="stylesheet" href="https://fonts.googleapis.com/css2?family=IBM+Plex+Sans:wght@400;500&display=swap">
<style>
  :root {
    --bg: #e1e2e5;
    --card: #ffffff;
    --brand: #a4004f;
    --ink: #1b1b1b;
    --dot: #c2c3c6;
    --link: #1f3f7a;
    --illus-a: #dfe3f3;
    --illus-b: #c9cfec;
  }
  * { box-sizing: border-box; margin: 0; padding: 0; }
  html, body { width: 1200px; height: 729px; overflow: hidden; }
  body {
    background: var(--bg);
    font-family: "IBM Plex Sans", Roboto, sans-serif;
    color: var(--ink);
    position: relative;
  }
  .slide {
    position: absolute;
    top: 65px;
    width: 309px;
    height: 585px;
    background: var(--card);
    box-shadow: 0 1px 4px rgba(0,0,0,0.06);
  }
  .slide--welcome { left: 75px; }
  .slide--account { left: 436px; }
  .slide--secure  { left: 811px; }

  .slide__illustration {
    position: absolute;
    border-radius: 6px;
    background: linear-gradient(135deg, var(--illus-a), var(--illus-b));
  }
  .slide__text {
    position: absolute;
    left: 0; right: 0;
    text-align: center;
  }
  .eyebrow { font-size: 16px; line-height: 20px; font-weight: 400; }
  .title { font-size: 27px; line-height: 31px; font-weight: 500; }
  .heading { font-size: 22px; line-height: 27px; font-weight: 500; }
  .lead { font-size: 14px; line-height: 21px; font-weight: 500; }
  .body { font-size: 13.5px; line-height: 19px; font-weight: 400; }
  .small { font-size: 12px; line-height: 16px; }

  .logon {
    position: absolute;
    left: 126px; top: 468px;
    width: 57px; height: 24px;
    border: 1.5px solid var(--link);
    color: var(--link);
    font-size: 11.5px;
    font-weight: 400;
    display: flex; align-items: center; justify-content: center;
    letter-spacing: 0.3px;
  }
  .pager {
    position: absolute;
    left: 0; right: 0;
    display: flex; justify-content: center; gap: 10px;
  }
  .pager span {
    width: 5.5px; height: 5.5px; border-radius: 50%;
    background: var(--dot);
  }
  .pager span.is-active { background: var(--brand); }

  .next {
    position: absolute;
    left: 0; right: 0; bottom: 0;
    height: 38px;
    background: var(--brand);
    color: #fff;
    font-size: 18px;
    font-weight: 500;
    display: flex; align-items: center; justify-content: center; gap: 5px;
  }
</style>
</head>
<body>

<section class="slide slide--welcome">
  <div class="slide__illustration" style="left:55px;top:13px;width:180px;height:146px;" role="img" aria-label="Illustration of a person working at a laptop surrounded by gears and workflow charts"></div>
  <p class="slide__text eyebrow" style="top:173px;">WELCOME TO</p>
  <h1 class="slide__text title" style="top:197px;">Meridale Brokers<br>Apply Online</h1>
  <p class="slide__text lead" style="top:270px;">You can apply online for your next<br>mortgage credit in about 20 minutes.</p>
  <p class="slide__text body" style="top:331px;">It’s easy, and we will guide<br>you all the way.</p>
  <p class="slide__text body" style="top:384px;">See the five simple steps that<br>you have to take!</p>
  <p class="slide__text small" style="top:440px;">Already have an account?</p>
  <a class="logon">LOGON</a>
  <div class="pager" style="top:520px;">
    <span class="is-active"></span><span></span><span></span><span></span><span></span><span></span><span></span>
  </div>
  <div class="next">Next
    <svg width="14" height="12" viewBox="0 0 14 12" fill="none" stroke="#fff" stroke-width="1.8"><path d="M1 1l5 5-5 5M7 1l5 5-5 5"/></svg>
  </div>
</section>

<section class="slide slide--account">
  <div class="slide__illustration" style="left:66px;top:35px;width:169px;height:161px;" role="img" aria-label="Illustration of a woman at a laptop connected to a flow of app screens"></div>
  <h2 class="slide__text heading" style="top:226px;">#1 Create your<br>personal account</h2>
  <p class="slide__text lead" style="top:295px;">You will need a valid email address<br>to create your account</p>
  <p class="slide__text body" style="top:358px;">We will send you a confirmation<br>email,make sure you click the link to<br>verify your email address</p>
  <div class="pager" style="top:497px;">
    <span></span><span class="is-active"></span><span></span><span></span><span></span><span></span><span></span>
  </div>
  <div class="next">Next
    <svg width="14" height="12" viewBox="0 0 14 12" fill="none" stroke="#fff" stroke-width="1.8"><path d="M1 1l5 5-5 5M7 1l5 5-5 5"/></svg>
  </div>
</section>

<section class="slide slide--secure">
  <div class="slide__illustration" style="left:62px;top:28px;width:186px;height:179px;" role="img" aria-label="Illustration of a person beside a large mobile phone with a padlock and sign-in screen"></div>
  <h2 class="slide__text heading" style="top:235px;">#2 Secure your account<br>with your mobile phone</h2>
  <p class="slide__text lead" style="top:305px;">You will need a valid mobile phone<br>number to enable two factor<br>authentication.</p>
  <p class="slide__text body" style="top:393px;">We will send you an SMS containing<br>a security code to verify your<br>mobile number</p>
  <div class="pager" style="top:497px;">
    <span></span><span></span><span class="is-active"></span><span></span><span></span><span></span><span></span>
  </div>
  <div class="next">Next
    <svg width="14" height="12" viewBox="0 0 14 12" fill="none" stroke="#fff" stroke-width="1.8"><path d="M1 1l5 5-5 5M7 1l5 5-5 5"/></svg>
  </div>
</section>

</body>
</html>
```